Business Card Design Project

Business Card design based on logo.
Updates

I need business card, letterhead, envelope, and if possible, Powerpoint slide template.

On front of business card: Just logo- and  my name and title:  Harriet Lindqvist, Principal

On reverse-logo and the rest of the contact info:

4871 Quarry Lane
Davis, CA 95618
650-318-2764
hl@brackenstudyworks.example

On letterhead-Just logo at top, at bottom  the rest-very small along the bottom

On PPT slide-just the logo.

I also want to try a few other colors-I like lime/dark grey (not black) but would like to try Sienna, maybe also indigo or bright blue-green.

I forgot to add-

On the business card-switch to vertical on reverse side and put:

Reverse side-switch to vertical and list:

Harriet Lindqvist
Principal
Bracken Study Works, LLC

650-318-2764

4871 Quarry Lane
Davis, CA 95618

Harriet Lindqvist
Principal

650-318-2764

4871 Quarry Lane
Davis, CA 95618

I have another project at the same time-for Stationery. Feel free to submit to that one also.

That one includes letterhead, envelope, PPT slide, folder cover sheet-HL

Industry/Entity Type

Business

Requirements
Must have
• Must use logo-preferably lime green version-with gray, not black or just 2-tone -logo on colored background.

```html
<!DOCTYPE html>
<html lang="en">
<head>
<meta charset="utf-8">
<title>Bracken Study Works – Business Cards</title>
<link rel="stylesheet" href="https://fonts.googleapis.com/css2?family=PT+Sans:wght@400;700&display=swap">
<style>
  :root {
    --backdrop: #161616;
    --lime: #9bb82f;
    --charcoal: #454547;
    --paper: #ffffff;
    --ink: #3e3e40;
    --black: #111111;
    --soft-white: #eeeeee;
  }
  * { margin: 0; padding: 0; box-sizing: border-box; }
  html, body { width: 1200px; height: 722px; overflow: hidden; }
  body {
    background: var(--backdrop);
    font-family: "PT Sans", sans-serif;
    position: relative;
  }
  .card {
    position: absolute;
    width: 525px;
    height: 300px;
    border-radius: 14px;
    overflow: hidden;
  }
  .card--contact { left: 58px; top: 47px; background: var(--paper); }
  .card--white { left: 612px; top: 47px; background: var(--paper); }
  .card--lime { left: 62px; top: 376px; background: var(--lime); height: 298px; }
  .card--dark { left: 612px; top: 376px; background: var(--charcoal); height: 298px; }

  .wordmark {
    position: absolute;
    display: flex;
    align-items: center;
    gap: 12px;
    font-weight: 400;
    letter-spacing: 0.18em;
    line-height: 1.15;
    text-transform: uppercase;
  }
  .wordmark__square { width: 22px; height: 22px; flex: none; }
  .wordmark__name { font-size: 28px; }

  .card--contact .wordmark { left: 34px; top: 110px; color: var(--ink); }
  .card--contact .wordmark__name { font-size: 22px; }
  .card--contact .wordmark__square { background: var(--lime); width: 18px; height: 18px; }

  .contact-panel {
    position: absolute;
    left: 287px; top: 0;
    width: 238px; height: 100%;
    background: var(--charcoal);
    border-left: 4px solid var(--lime);
    color: var(--soft-white);
    padding: 78px 12px 0 25px;
    font-size: 13.5px;
    line-height: 19px;
  }
  .contact-panel__name { color: var(--lime); font-weight: 700; font-size: 17px; line-height: 20px; }
  .contact-panel__title { margin-bottom: 12px; }
  .contact-list { list-style: none; margin-bottom: 12px; font-size: 11.5px; }
  .contact-list li { display: flex; align-items: center; gap: 6px; white-space: nowrap; }
  .contact-list svg { width: 10px; height: 10px; fill: var(--lime); flex: none; }
  .contact-panel__address { font-style: normal; }

  .centered { left: 0; right: 0; justify-content: center; }
  .card--white .wordmark { top: 128px; color: var(--ink); }
  .card--white .wordmark__square { background: var(--lime); }
  .card--lime .wordmark { top: 162px; color: var(--black); }
  .card--lime .wordmark__square { background: var(--black); }
  .card--dark .wordmark { top: 132px; color: var(--lime); }
  .card--dark .wordmark__name { font-size: 34px; }
  .card--dark .wordmark__square { background: var(--lime); width: 28px; height: 28px; }

  .web {
    position: absolute;
    left: 0; right: 0;
    text-align: center;
    font-size: 13px;
    letter-spacing: 0.16em;
  }
  .web__domain { color: var(--lime); }
  .card--white .web { top: 220px; color: var(--ink); }
  .card--lime .web { top: 244px; color: var(--paper); }
  .card--lime .web__domain { color: var(--paper); }
  .card--dark .web { top: 244px; color: var(--paper); }
</style>
</head>
<body>
  <section class="card card--contact">
    <div class="wordmark">
      <span class="wordmark__square"></span>
      <span class="wordmark__name">Bracken<br>Study Works</span>
    </div>
    <div class="contact-panel">
      <p class="contact-panel__name">YOUR NAME</p>
      <p class="contact-panel__title">Title</p>
      <ul class="contact-list">
        <li><svg viewBox="0 0 10 10"><path d="M2 0.5l2 2-1 1.3c.6 1.3 1.5 2.2 2.8 2.8l1.3-1 2 2-1.3 1.8C4.5 9 1 5.5.3 1.8z"/></svg>0987 654321</li>
        <li><svg viewBox="0 0 10 10"><path d="M1 4h8v4H1zM2.5 1h5l1 3h-7zM2 8h1.5v1.5H2zM6.5 8H8v1.5H6.5z"/></svg>0987 654321</li>
        <li><svg viewBox="0 0 10 10"><path d="M0 2.5h10v6H0zM0 2.5l5 3.5 5-3.5"/></svg>info@brackenstudyworks.example</li>
        <li><svg viewBox="0 0 10 10"><circle cx="5" cy="5" r="4.5"/></svg>www.brackenstudyworks.example</li>
      </ul>
      <address class="contact-panel__address">00 Floor Complex<br>Street City Name 000 111</address>
    </div>
  </section>

  <section class="card card--white">
    <div class="wordmark centered">
      <span class="wordmark__square"></span>
      <span class="wordmark__name">Bracken Study Works</span>
    </div>
    <p class="web">www.<span class="web__domain">brackenstudyworks</span>.example</p>
  </section>

  <section class="card card--lime">
    <div class="wordmark centered">
      <span class="wordmark__square"></span>
      <span class="wordmark__name">Bracken Study Works</span>
    </div>
    <p class="web">www.<span class="web__domain">brackenstudyworks</span>.example</p>
  </section>

  <section class="card card--dark">
    <div class="wordmark centered">
      <span class="wordmark__square"></span>
      <span class="wordmark__name">Bracken</span>
    </div>
    <p class="web">www.<span class="web__domain">brackenstudyworks</span>.example</p>
  </section>
</body>
</html>
```